International aerospace industry business needs a new brochure

We need to make a new Brochure 4 pages A4:
- like the old one (file Vermondix_test_coupons_thermal_spray.pdf)
- with the new text (tekst_na_ulotke_v9.docx)
- with the new design as in email graphic (20201019_FINAL_Test Coupons v2.psd or .png).

Requirements
Must have
• design as in email graphic (20201019_FINAL_Test Coupons v2.psd or .png)
with the new text (tekst_na_ulotke_v9.docx)
Nice to have
• photos with our employees on production floor may be used.

```html
<!DOCTYPE html>
<html lang="en">
<head>
<meta charset="utf-8">
<title>Why to use tight tolerance test coupons?</title>
<link href="https://fonts.googleapis.com/css2?family=Open+Sans:wght@400;600;700;800&display=swap" rel="stylesheet">
<style>
  :root {
    --navy: #1d3a5c;
    --navy-dark: #15304f;
    --orange: #f28c1e;
    --grey-band: #eceef1;
    --grey-box: #f1f2f4;
    --text: #2b2b2b;
    --green: #6fbf3c;
    --red: #e0413b;
    --photo: #9ea7b0;
    --white: #ffffff;
  }
  * { box-sizing: border-box; margin: 0; padding: 0; }
  html, body { width: 849px; height: 1200px; overflow: hidden; background: var(--white); }
  body { font-family: "Open Sans", Arial, sans-serif; color: var(--text); position: relative; }

  .headline-band { position: absolute; left: 0; top: 0; width: 849px; height: 38px; background: var(--grey-band); }
  .headline { position: absolute; left: 40px; top: 5px; font-size: 22px; font-weight: 800; color: var(--navy); }

  .intro { position: absolute; left: 40px; top: 46px; width: 770px; font-size: 11.6px; line-height: 1.42; }
  .intro p { margin-bottom: 1px; }
  .ticks { list-style: none; margin: 0 0 2px 24px; }
  .ticks li { position: relative; padding-left: 18px; }
  .ticks li::before { content: ""; position: absolute; left: 2px; top: 3px; width: 5px; height: 9px;
    border: solid var(--orange); border-width: 0 2.5px 2.5px 0; transform: rotate(40deg); }

  .chart { position: absolute; left: 125px; top: 345px; width: 600px; height: 340px; }

  .accessories-band { position: absolute; left: 0; top: 698px; width: 849px; height: 24px; }
  .accessories-band .label { position: absolute; left: 160px; width: 530px; height: 24px; background: var(--orange);
    color: var(--white); font-weight: 800; font-size: 13px; letter-spacing: 1px; text-align: center; line-height: 24px; }

  .photo { position: absolute; left: 100px; top: 732px; width: 172px; height: 108px;
    background: linear-gradient(135deg, #c5ccd3, var(--photo)); }
  .accessories-box { position: absolute; left: 282px; top: 732px; width: 455px; height: 108px;
    background: var(--grey-box); padding: 8px 14px; font-size: 11.3px; line-height: 1.45; }
  .accessories-box ul { list-style: none; margin: 4px 0 0 14px; }
  .accessories-box li::before { content: "\2022"; color: var(--orange); margin-right: 8px; }

  .contact-panel { position: absolute; left: 0; top: 1008px; width: 372px; height: 142px; background: var(--navy); color: var(--white);
    padding: 14px 0 0 62px; font-size: 12.5px; line-height: 1.38; }
  .contact-panel .firm { font-weight: 700; font-size: 13.5px; }
  .contact-panel svg { position: absolute; left: 22px; }
  .contact-note { position: absolute; left: 392px; top: 1012px; width: 440px; font-size: 11.6px; line-height: 1.4; }
  .brand { position: absolute; left: 560px; top: 1084px; font-size: 26px; font-weight: 800; color: var(--navy); }
  .brand-mark { display: inline-block; width: 14px; height: 14px; background: var(--orange); margin-right: 8px; vertical-align: 2px; }

  .url-bar { position: absolute; left: 0; top: 1150px; width: 849px; height: 50px; background: var(--navy-dark);
    color: var(--white); font-weight: 700; font-size: 21px; text-align: center; line-height: 50px; letter-spacing: .5px; }
</style>
</head>
<body>
  <div class="headline-band"></div>
  <h1 class="headline">Why to use tight tolerance test coupons?</h1>

  <section class="intro">
    <p>Thermal Spray facilities especially in aerospace industry often need to check coating quality on test specimens by destructive tests e.g. tensile / bond strength test. This need to be done for basically three reasons:</p>
    <ul class="ticks">
      <li>to obtain approval for coating in qualification process,</li>
      <li>continuous monitor of coating consistency,</li>
      <li>decrease the frequency of testing according to Reduced Testing / Sampling procedure.</li>
    </ul>
    <p>The acceptance or magnitude of above activities often depends on a process capability / performance index CPK / PPK calculated with the test results during Statistical Process Control e.g. the more stable test results are the higher testing reduction can be obtained and maintained. There are many factors of test results variation but one of them is quality of test specimens – and here we have a solution for your facility. Using our made test buttons you can:</p>
    <ul class="ticks">
      <li>obtain better test results for coating qualification,</li>
      <li>improve reduced testing and hold it on a high level.</li>
    </ul>
    <p>Please see a visualisation on the graph below.</p>
  </section>

  <svg class="chart" viewBox="0 0 600 340" font-family="Open Sans, Arial, sans-serif">
    <rect x="0.5" y="0.5" width="599" height="339" fill="#fafafa" stroke="#bfc3c8"/>
    <g font-weight="700" font-size="11" fill="#333" text-anchor="middle">
      <text x="300" y="22">STATISTICAL PROCESS CONTROL CHART</text>
      <text x="300" y="36">TENSILE / BOND STRENGTH TEST OF COATING</text>
      <text x="300" y="50">COMPARISON OF TEST BUTTONS FABRICATION</text>
    </g>
    <rect x="60" y="65" width="470" height="190" fill="#fff" stroke="#d6d9dc"/>
    <g stroke="#eceef0">
      <line x1="60" y1="103" x2="530" y2="103"/><line x1="60" y1="141" x2="530" y2="141"/>
      <line x1="60" y1="179" x2="530" y2="179"/><line x1="60" y1="217" x2="530" y2="217"/>
    </g>
    <text x="30" y="160" font-size="10" fill="#333" transform="rotate(-90 30 160)" text-anchor="middle">PRESSURE [PSI]</text>
    <g stroke-dasharray="6 4" stroke-width="1.5">
      <line x1="60" y1="92" x2="530" y2="92" stroke="var(--red)"/>
      <line x1="60" y1="232" x2="530" y2="232" stroke="var(--red)"/>
      <line x1="60" y1="138" x2="530" y2="138" stroke="var(--green)"/>
      <line x1="60" y1="176" x2="530" y2="176" stroke="var(--green)"/>
    </g>
    <line x1="60" y1="157" x2="530" y2="157" stroke="var(--orange)" stroke-width="2"/>
    <polyline fill="none" stroke="var(--red)" stroke-width="2"
      points="72,160 99,182 126,125 153,218 180,146 207,112 234,205 261,168 288,135 315,225 342,158 369,190 396,118 423,200 450,148 477,172 504,128"/>
    <polyline fill="none" stroke="var(--green)" stroke-width="2"
      points="72,150 99,165 126,146 153,163 180,149 207,158 234,153 261,166 288,147 315,158 342,150 369,162 396,152 423,145 450,160 477,151 504,156"/>
    <rect x="538" y="96" width="52" height="30" fill="#fff" stroke="var(--red)"/>
    <text x="564" y="109" font-size="9" fill="var(--red)" text-anchor="middle">Low</text>
    <text x="564" y="121" font-size="9" fill="var(--red)" text-anchor="middle">Ppk/Cpk</text>
    <rect x="538" y="186" width="52" height="30" fill="#fff" stroke="var(--green)"/>
    <text x="564" y="199" font-size="9" fill="var(--green)" text-anchor="middle">High</text>
    <text x="564" y="211" font-size="9" fill="var(--green)" text-anchor="middle">Ppk/Cpk</text>
    <g font-size="8.5" fill="#333" text-anchor="middle">
      <text x="72" y="268">477</text><text x="99" y="268">492</text><text x="126" y="268">497</text><text x="153" y="268">511</text>
      <text x="180" y="268">518</text><text x="207" y="268">519</text><text x="234" y="268">526</text><text x="261" y="268">561</text>
      <text x="288" y="268">582</text><text x="315" y="268">583</text><text x="342" y="268">589</text><text x="369" y="268">646</text>
      <text x="396" y="268">648</text><text x="423" y="268">649</text><text x="450" y="268">666</text><text x="477" y="268">668</text>
      <text x="504" y="268">669</text>
    </g>
    <text x="295" y="282" font-size="10" fill="#333" text-anchor="middle">BATCH NUMBER</text>
    <g font-size="9" fill="#333">
      <line x1="60" y1="297" x2="85" y2="297" stroke="var(--red)" stroke-width="2"/><text x="90" y="300">specimens made by turning</text>
      <line x1="300" y1="297" x2="325" y2="297" stroke="var(--green)" stroke-width="2"/><text x="330" y="300">Vermondix made specimens</text>
      <line x1="60" y1="313" x2="85" y2="313" stroke="var(--red)" stroke-width="1.5" stroke-dasharray="5 3"/><text x="90" y="316">+/- 3σ of turning specimens</text>
      <line x1="300" y1="313" x2="325" y2="313" stroke="var(--green)" stroke-width="1.5" stroke-dasharray="5 3"/><text x="330" y="316">+/- 3σ of Vermondix made specimens</text>
      <line x1="60" y1="329" x2="85" y2="329" stroke="var(--orange)" stroke-width="2"/><text x="90" y="332">the same mean for both fabrication</text>
    </g>
  </svg>

  <div class="accessories-band"><div class="label">CUSTOM LABORATORY ACCESSORIES</div></div>
  <div class="photo" role="img" aria-label="Photo of a machined laboratory fixture for test coupons"></div>
  <div class="accessories-box">
    <p>Machining of laboratory related tools:</p>
    <ul>
      <li>Gravity or pressure type V-grooved curing fixture for Tensile Bond Strength test of coating</li>
      <li>Loading fixture</li>
      <li>and more....</li>
    </ul>
  </div>

  <address class="contact-panel" style="font-style:normal">
    <svg width="26" height="34" viewBox="0 0 26 34" style="top:16px"><path d="M13 1a12 12 0 0 0-12 12c0 9 12 20 12 20s12-11 12-20A12 12 0 0 0 13 1z" fill="var(--orange)"/><circle cx="13" cy="13" r="5" fill="var(--navy)"/></svg>
    <div class="firm">trial.samples</div>
    <div>Vermondix Sp. z o.o.</div>
    <div>Kwiatowa 14</div>
    <div>02-811 Lindenbrook, Poland</div>
    <svg width="22" height="22" viewBox="0 0 24 24" style="top:90px"><path d="M6.6 10.8a15 15 0 0 0 6.6 6.6l2.2-2.2c.3-.3.7-.4 1-.2 1.1.4 2.3.6 3.6.6.6 0 1 .4 1 1V20c0 .6-.4 1-1 1A17 17 0 0 1 3 4c0-.6.4-1 1-1h3.5c.6 0 1 .4 1 1 0 1.3.2 2.5.6 3.6.1.3 0 .7-.2 1z" fill="var(--orange)"/></svg>
    <div>+48 500 123 456</div>
    <svg width="22" height="18" viewBox="0 0 24 18" style="top:112px"><rect x="1" y="1" width="22" height="16" rx="2" fill="var(--orange)"/><path d="M2 3l10 7 10-7" fill="none" stroke="var(--navy)" stroke-width="2"/></svg>
    <div>info@vermondix.com</div>
  </address>

  <p class="contact-note">Please feel free to contact us if you have any questions or need further information. It will be pleasure for us to provide free samples of test coupons for your needs.</p>
  <div class="brand"><span class="brand-mark"></span>trial.samples</div>

  <div class="url-bar">https://trial.samples</div>
</body>
</html>
```